Corvale Year 9 Curriculum Model

We need a graphic that communicates all the overlapping elements of our new curriculum. Perhaps it could involve a series of concentric circles moving out from the centre:
1. the "Ideal Learner" profile at the centre with the school's logo behind it (see uploaded file).
2. The words of the "General Capabilities" from the Australian national curriculum in the next circle moving out of centre: "Ethical Understanding" "Literacy" "Numeracy" "Intercultural Awareness" "ICT Capacity" "Critical and Creative Thinking" "Personal and Social Capability"
3. Next circle out has the subjects: "Mathematics" "English" "Languages" "Health and Physical Education" "Technology" "Religious Education" "Humanities" "Arts" "Science"
4. Next Circle out has the title "Community" and then less important, the words "Local" "Regional" "National"
5. Next circle out is simple called "World"
6. Next circle out is simply called "Future"
IF there is a way to make it look not too bad...:Overlaying all the other aspects, floating somewhere, are the 3 significant priorities for the curriculum: Asia, Indigenous Culture and Sustainability

Year 9 (15 year old) school students and their parents, as well as teachers and other visitors to the school. It will be used to explain the curriculum and have on the walls as a reminder.

School

• All of the words in the brief, with a relational dimension for each.

```html
<!DOCTYPE html>
<html lang="en">
<head>
<meta charset="utf-8">
<title>Corvale Year 9 Curriculum Model</title>
<link rel="stylesheet" href="https://fonts.googleapis.com/css2?family=Marcellus&family=Crimson+Text&display=swap">
<style>
  :root {
    --bg-light: #f6fbfd;
    --bg-soft: #cfe6f0;
    --ring-dark: #2a9a84;
    --ring-mint: #4deab7;
    --white: #ffffff;
    --subjects: #c21ee2;
    --capabilities: #3913d6;
    --community: #f28c10;
    --world: #d3127e;
    --future: #74d900;
    --learner: #38b6b8;
    --learner-edge: #2aa6a8;
  }
  html, body {
    margin: 0;
    padding: 0;
    width: 1200px;
    height: 900px;
    overflow: hidden;
  }
  .canvas {
    display: block;
    width: 1200px;
    height: 900px;
  }
  .priority {
    font-family: "Marcellus", serif;
    font-size: 37px;
    fill: var(--white);
    letter-spacing: 1px;
  }
  .circle-title {
    font-family: "Marcellus", serif;
    fill: var(--white);
    text-anchor: middle;
  }
  .circle-list {
    font-family: "Crimson Text", serif;
    fill: var(--white);
    text-anchor: middle;
  }
  .dotted-arc {
    fill: none;
    stroke: var(--white);
    stroke-width: 2.6;
    stroke-linecap: round;
    stroke-dasharray: 0 7;
  }
  .learner-word {
    font-family: "Marcellus", serif;
    font-size: 31px;
    fill: var(--white);
    text-anchor: middle;
  }
  .school-name {
    font-family: "Crimson Text", serif;
    font-size: 13px;
    fill: var(--white);
    text-anchor: middle;
  }
</style>
</head>
<body>
<svg class="canvas" viewBox="0 0 1200 900" xmlns="http://www.w3.org/2000/svg">
  <defs>
    <radialGradient id="backdrop" cx="50%" cy="50%" r="75%">
      <stop offset="0%" stop-color="var(--bg-light)"/>
      <stop offset="100%" stop-color="var(--bg-soft)"/>
    </radialGradient>
    <path id="priority-track" d="M600,72 A378,378 0 1 1 600,828 A378,378 0 1 1 600,72"/>
    <path id="community-track" d="M667,372 A95,95 0 0 1 857,372"/>
    <path id="ideal-track" d="M556,453 A44,44 0 0 1 644,453"/>
    <path id="learner-track" d="M539,453 A61,61 0 0 0 661,453"/>
  </defs>

  <rect class="backdrop" width="1200" height="900" fill="url(#backdrop)" role="img" aria-label="Soft pale blue background with a faint interlocking circle pattern"/>

  <g class="priority-ring">
    <circle cx="600" cy="450" r="435" fill="var(--ring-dark)"/>
    <circle cx="600" cy="450" r="414" fill="var(--ring-mint)"/>
    <circle cx="600" cy="450" r="366" fill="var(--white)"/>
    <text class="priority"><textPath href="#priority-track" startOffset="1790" text-anchor="middle">Asia</textPath></text>
    <text class="priority"><textPath href="#priority-track" startOffset="575" text-anchor="middle">Indigenous Culture</textPath></text>
    <text class="priority"><textPath href="#priority-track" startOffset="1188" text-anchor="middle">Sustentability</textPath></text>
  </g>

  <g class="circle world">
    <circle cx="727" cy="578" r="120" fill="var(--world)"/>
    <path class="dotted-arc" d="M776,485 A108,108 0 1 1 628,620"/>
    <text class="circle-title" x="723" y="576" font-size="23">World</text>
  </g>

  <g class="circle future">
    <circle cx="517" cy="608" r="120" fill="var(--future)"/>
    <path class="dotted-arc" d="M625,622 A108,108 0 0 1 617,650"/>
    <path class="dotted-arc" d="M420,548 A108,108 0 0 1 432,528"/>
    <text class="circle-title" x="517" y="615" font-size="22">Future</text>
  </g>

  <g class="circle subjects">
    <circle cx="578" cy="290" r="122" fill="var(--subjects)"/>
    <path class="dotted-arc" d="M520,190 A110,110 0 0 1 688,296"/>
    <text class="circle-list" font-size="14.5">
      <tspan x="581" y="192">Mathematics</tspan>
      <tspan x="581" y="210">English</tspan>
      <tspan x="581" y="228">Languages</tspan>
      <tspan x="581" y="246">Health and Physical</tspan>
      <tspan x="581" y="264">Education</tspan>
      <tspan x="581" y="282">Technology</tspan>
      <tspan x="581" y="300">Religious Education</tspan>
      <tspan x="581" y="318">Humanities</tspan>
      <tspan x="581" y="336">Arts</tspan>
      <tspan x="581" y="353">Science</tspan>
    </text>
  </g>

  <g class="circle community">
    <circle cx="762" cy="370" r="120" fill="var(--community)"/>
    <path class="dotted-arc" d="M868,352 A108,108 0 0 1 778,477"/>
    <text class="circle-title" font-size="22"><textPath href="#community-track" startOffset="50%">Community</textPath></text>
    <text class="circle-list" font-size="13.5">
      <tspan x="761" y="357">Local</tspan>
      <tspan x="761" y="374">Regional</tspan>
      <tspan x="761" y="391">National</tspan>
    </text>
  </g>

  <g class="circle capabilities">
    <circle cx="425" cy="412" r="120" fill="var(--capabilities)"/>
    <path class="dotted-arc" d="M474,316 A108,108 0 0 0 318,400 A108,108 0 0 0 440,519"/>
    <text class="circle-title" font-size="22">
      <tspan x="430" y="356">General</tspan>
      <tspan x="426" y="380">Capabilities</tspan>
    </text>
    <text class="circle-list" font-size="11.5">
      <tspan x="425" y="403">Ethical Understanding</tspan>
      <tspan x="425" y="417">Literacy</tspan>
      <tspan x="425" y="431">Numeracy</tspan>
      <tspan x="425" y="445">Intercultural Awareness</tspan>
      <tspan x="425" y="459">ICT Capacity</tspan>
      <tspan x="425" y="473">Critical and Creative Thinking</tspan>
      <tspan x="425" y="487">Personal and Social Capability</tspan>
    </text>
  </g>

  <g class="ideal-learner">
    <circle cx="600" cy="453" r="92" fill="var(--learner-edge)"/>
    <circle cx="600" cy="453" r="86" fill="var(--white)"/>
    <circle cx="600" cy="453" r="82" fill="var(--learner)"/>
    <text class="learner-word"><textPath href="#ideal-track" startOffset="50%">Ideal</textPath></text>
    <text class="learner-word"><textPath href="#learner-track" startOffset="50%">Learner</textPath></text>
    <text class="school-name" x="600" y="476">Corvale</text>
  </g>
</svg>
</body>
</html>
```